32 x 24 Swinging Real Estate Yard Sign

We are looking to design a new sign for our business to focus on the remodeling of homes to sell. We are looking to have a yard sign that gets peoples attention and is informational. The headline will be "The Secret to Top Dollar? Remodel First.". We remodel homes for sellers with no up front cost, as they simply pay at closing. This link has more info, https://bramblecresthomes.com/Remodel
The message we want to convey to those seeing the sign is we are a one stop shop, who can renovate your home and sell it for no stress. We are licensed real estate agents and licensed contractors.
Both of these license numbers and info need to be on the design:
CADRE #02794613
Contractors License #1178524
Email: info@bramblecresthomes.com
Phone: (408)614-2907
I'll attach a sample sign we have for our agents normally as well as all brand art work.
• Pantone Colors
o #172A41
Dark blue
o #4381B1
Medium blue
o #6FA6CC
Light blue
Target Market(s)
Residential Real Estate Sellers
Industry/Entity Type
Real Estate
Colors
Designer to choose colors to be used in the design.

```html
<!DOCTYPE html>
<html lang="en">
<head>
<meta charset="utf-8">
<title>Bramblecrest Homes – Remodel First Yard Sign</title>
<link rel="stylesheet" href="https://fonts.googleapis.com/css2?family=Montserrat:wght@700;800&family=Poppins:wght@400;500;600&display=swap">
<style>
  :root {
    --backdrop: #c4c4c4;
    --navy: #172a41;
    --steel: #3b6a8f;
    --white: #ffffff;
  }
  * { margin: 0; padding: 0; box-sizing: border-box; }
  html, body {
    width: 956px; height: 1200px; overflow: hidden;
    background: var(--backdrop);
  }
  .sign {
    position: absolute; left: 92px; top: 86px;
    width: 771px; height: 1027px;
    background: var(--steel);
    box-shadow: 0 6px 18px rgba(0,0,0,0.28);
    overflow: hidden;
  }
  .sign-swoosh { position: absolute; inset: 0; width: 100%; height: 100%; }
  .brand {
    position: absolute; left: 0; right: 0; top: 58px;
    text-align: center;
    font-family: "Poppins", sans-serif; font-weight: 600;
    font-size: 40px; letter-spacing: 1px;
    color: var(--navy);
  }
  .headline {
    position: absolute; left: 0; right: 0;
    text-align: center; white-space: nowrap;
    font-family: "Montserrat", sans-serif;
    line-height: 1;
  }
  .headline-question {
    font-weight: 700; font-size: 74px; letter-spacing: -1px;
    color: var(--steel);
  }
  .headline-question.line-1 { top: 190px; left: 40px; }
  .headline-question.line-2 { top: 264px; left: 40px; }
  .dollar-o {
    display: inline-block; width: 76px; height: 76px;
    border-radius: 50%; background: var(--steel); color: var(--white);
    font-size: 58px; line-height: 76px; text-align: center;
    vertical-align: -10px; margin: 0 1px;
  }
  .headline-answer {
    font-weight: 800; font-size: 104px; letter-spacing: -1px;
    color: var(--navy);
  }
  .headline-answer.line-1 { top: 356px; left: 20px; }
  .headline-answer.line-2 { top: 456px; left: -10px; }
  .phone {
    position: absolute; left: 0; right: 0; top: 662px;
    text-align: center; white-space: nowrap;
    font-family: "Montserrat", sans-serif; font-weight: 700;
    font-size: 88px; letter-spacing: -1px; line-height: 1;
    color: var(--white);
  }
  .email-band {
    position: absolute; left: 0; right: 0; top: 774px; height: 99px;
    background: var(--navy);
    display: flex; align-items: center; justify-content: center;
    font-family: "Poppins", sans-serif; font-weight: 500;
    font-size: 44px; color: var(--white);
  }
  .licenses {
    position: absolute; left: 0; right: 0; top: 888px;
    text-align: center;
    font-family: "Poppins", sans-serif; font-weight: 500;
    font-size: 41px; line-height: 51px; color: var(--white);
  }
</style>
</head>
<body>
  <main class="sign">
    <svg class="sign-swoosh" viewBox="0 0 1210 1612" preserveAspectRatio="none" aria-hidden="true">
      <path fill="#172a41" d="M735,955 C950,940 1120,840 1210,690 L1210,860 C1100,935 900,965 735,955 Z"/>
      <path fill="#ffffff" d="M0,0 L985,0 C1120,180 1160,520 1010,795 C1090,700 1160,620 1210,545 L1210,690 C1120,840 950,940 735,955 C500,965 250,920 0,810 Z"/>
    </svg>

    <div class="brand">BRAMBLECREST HOMES</div>

    <h1>
      <span class="headline headline-question line-1">THE SECRET TO</span>
      <span class="headline headline-question line-2">TOP D<span class="dollar-o">$</span>LLAR?</span>
      <span class="headline headline-answer line-1">REMODEL</span>
      <span class="headline headline-answer line-2">FIRST</span>
    </h1>

    <p class="phone">(408)614-2907</p>
    <p class="email-band">info@bramblecresthomes.com</p>
    <p class="licenses">CADRE #02794613<br>Contractors License #1178524</p>
  </main>
</body>
</html>
```